Packaging and labelling for Swiss made Organic CBD Oil

Visit our website www.clearleafmerida.example
We have not put any product on yet as require packaging and label design .
Website will give you a great feel for the company and how we have used
the logo . The Vextora cbd product shown is a company similar to ourselves with similar core values , we liked the clean packaging design they have .

Im happy if you want use the mandala symbol in our logo separate from
KELVORA, to separate and use the mandala symbol as a larger icon than
it appears in our logo
Clean , Pure , organic feel. Like the product to look pharmaceutical and life changing not gimmicky.
Colours to go with or be the same as our logo colours
But not too cold and clinical
Bottle size 84mm x 25mm
Label size 75mm x 30mm
Box 30mm x 30mm x 100mm
6 products
Full Spectrum :
500mg CBD (5%)
1000mg CBD ( 10% )
1500mg CBD (15%)
2000mg CBD ( 20% )
Broad spectrum THC Free
500mg CBD (5%)
Pets
500mg Broad Spectrum THC Free
Updates

Would like the design to be more modern than traditional

LABEL Information Front of Bottle - Logo KELVORA & Mandala - Mandala can be used separately as design symbol Organic Cannabis Oil 1500mg CBD (15%) Ful Spectrum 10ml Back of bottle Ingredients: Organic Cannabis Oil Extract Organic Sunflower Seed Oil THC - 0.2% Certified Swiss Organic Cultivation Shake well before use. Store in a cool , dry place and out of the each of children BOX information Front and rear Logo - KELVORA & Mandala - Mandala can be used separately as a design symbol Organic Cannabis Oil 1500mg CBD (15%) Full Spectrum Sides x 2 This product is a food supplement and is not intended to diagnose, treat, cure or prevent any disease If you are pregnant, lactating or taking any medication consult your health care practitioner Suitable for vegetarians and vegans Ingredients Organic Cannabis Oil extract Organis Sunflower Oil Store in a cool ,dry place, out of the reach of children Recommended Use 1-5 drops ( 1 drop = 7.5mg CBD ) Subject to body weight and personal requirement - visit www.clearleafmerida for more information 100% Natural 100% Organic GMO free 100% Vegan ( symbol with each ) Expiry date see bottle label Cultivated and manufactured in Switzerland

Target Market(s)

age 40 - 80

Font styles to use
Other font styles liked:
• In our website we have used Open Sans for the copy and Lato for headings .

Requirements
Must have
• look like an Industry leader
Kelvora will change the quality of peoples lives and in some cases may
even save lives so want look powerful and credible
Our Mission is - Through Delivering Pure , Premium , Organic products we will educate, inform and help people achieve healthier , happier lifestyles
Nice to have
• Colours to look good with our logo colours or be the same as our logo
colours
Logo Font - Avenir Black and Avenir Book

Font used in website - Content - Open Sans / Headings - Lato
If you have another font for the packaging information that will go well with
our logo, I'm happy for you to use your skills

```html
<!DOCTYPE html>
<html lang="en">
<head>
<meta charset="utf-8">
<title>Kelvora Organic Cannabis Oil – Bottle Label</title>
<link rel="stylesheet" href="https://fonts.googleapis.com/css2?family=Nunito+Sans:wght@700&family=Lato:wght@300;400&display=swap">
<style>
  :root {
    --backdrop: #625370;
    --label-grey: #8c9294;
    --label-grey-light: #979d9f;
    --wordmark: #ffffff;
    --accent-mint: #8fd3cc;
    --title-gold: #efe2ae;
    --strength-white: #f4f4f2;
    --mandala-gold: #efe6c2;
    --mandala-rose: #e9b9bd;
  }
  * { margin: 0; padding: 0; box-sizing: border-box; }
  html, body {
    width: 1200px;
    height: 936px;
    overflow: hidden;
    background: var(--backdrop);
  }
  .canvas {
    position: relative;
    width: 1200px;
    height: 936px;
    display: flex;
    align-items: center;
    justify-content: center;
  }
  .front-label {
    position: relative;
    width: 320px;
    height: 860px;
    background: linear-gradient(90deg, var(--label-grey) 0%, var(--label-grey-light) 45%, var(--label-grey) 100%);
    overflow: hidden;
  }
  .brand {
    position: absolute;
    top: 118px;
    left: 0;
    right: 0;
    display: flex;
    align-items: center;
    justify-content: center;
    gap: 12px;
  }
  .brand-dot {
    width: 16px;
    height: 16px;
    border-radius: 50%;
    background: var(--accent-mint);
  }
  .brand-name {
    font-family: "Nunito Sans", sans-serif;
    font-weight: 700;
    font-size: 44px;
    letter-spacing: 1px;
    color: var(--wordmark);
    line-height: 1;
  }
  .product-name {
    position: absolute;
    top: 282px;
    left: 0;
    right: 0;
    text-align: center;
    font-family: "Lato", sans-serif;
    font-weight: 300;
    font-size: 30px;
    color: var(--title-gold);
    letter-spacing: 0.3px;
  }
  .strength {
    position: absolute;
    top: 508px;
    left: 0;
    right: 0;
    text-align: center;
    font-family: "Lato", sans-serif;
    font-weight: 400;
    font-size: 22px;
    color: var(--strength-white);
  }
  .mandala-cluster {
    position: absolute;
    left: 0;
    bottom: 0;
    width: 320px;
    height: 290px;
    background:
      radial-gradient(circle at 28% 55%, rgba(239,230,194,0.55) 0%, rgba(239,230,194,0) 38%),
      radial-gradient(circle at 58% 25%, rgba(233,185,189,0.5) 0%, rgba(233,185,189,0) 34%),
      radial-gradient(circle at 80% 62%, rgba(233,185,189,0.5) 0%, rgba(233,185,189,0) 34%);
  }
</style>
</head>
<body>
  <main class="canvas">
    <section class="front-label" aria-label="Kelvora front bottle label">
      <div class="brand">
        <span class="brand-dot" aria-hidden="true"></span>
        <span class="brand-name">KELVORA</span>
      </div>
      <p class="product-name">Organic Cannabis Oil</p>
      <p class="strength">1500mg</p>
      <div class="mandala-cluster" role="img" aria-label="Cluster of three overlapping line-art mandalas in pale gold and soft rose"></div>
    </section>
  </main>
</body>
</html>
```